New web/graphic designs required to improve existing ecommerce site.

Initial outline of project:
This project is for new designs to fit into areas of existing webpages - specifically:-
Objective 1 - Produce 8 home page design proposals (design for central area of page only, not whole page)
Objective 2 - Produce 5 designs for page header banners (950px x 84px images)
Objective 3 - Produce 10 designs for help guide covers (316px x 410px images)
Also, on a more general note:
Objective 4 - Review and suggest improvements for other areas website. (This may lead to further design work)
-
Introduction to the Periodical Bazaar website:
The Periodical Bazaar website is a marketplace where back-issue hobby magazines can be bought and sold, and in some cases downloaded & viewed in digital form. The ‘sellers’ of the magazines will be both traders and private individuals. Trade sellers will also be able to sell magazine subscriptions and have ‘Promotion Pages’ about themselves and/or their magazine titles on the site. Other forms of advertising will also be available on the site for any commercial advertisers who want it, particularly for companies supplying the various hobbies covered.
Users of the website can locate magazines of interest to them by browsing through the hobby / category sections of the site, or by doing keyword searches for issues containing articles on specific topics.
The site is split-up into sections dealing with magazines about specific hobby subjects – ie., cars, motorbikes, railway, aviation, boating etc. Although part of the larger site, each of these sections is largely self-contained, with many users only ever browsing in the section related to their hobby. As such, each section effectively has it’s own home page, which will duplicate much of the information shown on the main home page. These multiple ‘section home pages’ will be promoted in their own right via URLs specific to that hobby. Currently there are 8 sections, but this number is expected to increase as the site grows.
This website is still being developed, but is close to launch; as such the website is fully functional but a lot of content is missing - please bear this in mind when viewing the site, and feel free to ask for clarification if anything is unclear.
The new website is currently at: http://www2.periodicalbazaar.co.uk
This website will replace several existing sites:-
http://www.periodicalbazaar.co.uk
http://www.twowheel-journals.co.uk
http://www.skyward-journals.co.uk
http://www.drivepapers.co.uk
http://www.trackside-journals.co.uk
http://www.scalecraft-journals.co.uk
-
Design notes:
The overall design is fairly conventional and very much ‘functionality’ driven, the website being at it’s heart an ecommerce system with some fairly complex features. Nevertheless I want the site to appear simple and modern in appearance, being somewhere between an ‘all style’ Web 2.0-type site (eg. tintly.io), and an ‘all function’ conventional trading site (eg. Bravlo, Quibb etc). A good example of a style of site which I would like to emulate is PostGecko – a complex and large site made to look friendly and approachable by the use of simple, clear design, bold colour and a sense of humour.
To explain further what is required I have prepared various image documents which include more detailed notes on the various objectives for this project. There is a lot of information in these documents - please read them carefully:-
Objective 1:
- Produce 1 'Main Home Page' design proposal
- Produce 8 'Section Home Page' design proposals - one each for these sections: Railway, Boating, Aviation, Cycling, Automotive, Motorcycling, Men's Lifestyle, Modelling
More information on Objective 1 is given in these image documents:
http://www.filenook.net/Home_Page_Designs-Purpose.gif
http://www.filenook.net/Home_Page_Designs-Areas.gif
http://www.filenook.net/Section_Home_Pages-1.gif
http://www.filenook.net/Section_Home_Pages-2.gif
-
Objective 2:
- Produce 5 designs for page header banners (950px x 84px images)
More information on Objective 2 is given in this image document:
http://www.filenook.net/Page_Header_Banners.gif
-
Objective 3:
- Produce 10 designs for help guide covers (316px x 410px images)
http://www.filenook.net/Help_Guide_Covers.gif
-
Objective 4:
- Review and suggest improvements for other areas website
I would like the designer to spend some time looking at the whole of the current website, and suggest any areas that can be improved. I am not looking for a wholesale re-design - the overall layout of the site and major design elements such as the navigation system - are essentially fixed - however, many graphical elements can be changed, as can any text content (including text content within the navigation system).
Improvements which are suggested may lead to additional design work either as part of this project, or as subsequent projects in their own right.
-
Designers are very welcome to contact me to discuss any aspect of this project, or if more information is required about the website or the designs required.
I'm happy to guarantee this project in due course, if there is positive reaction to the project from potential designers interested in submitting designs. This is the second project I have run on ArtBrigade - the first one was successful and resulted in the Flash animation that is currently on the homepage of the website.
UPDATE 11/10/11:
I've created some new documents to illustrate the sort of designs I am looking for for the Main Home Page and Section Home Pages:
Very rough examples of the sort of style I am looking for:
http://www.filenook.net/Rough_Main_Home_Page_1.jpg
http://www.filenook.net/Rough_Main_Home_Page_2.jpg
http://www.filenook.net/Rough_Main_Home_Page_3.jpg
http://www.filenook.net/Rough_Main_Home_Page_4.jpg
http://www.filenook.net/Rough_Main_Home_Page_5.jpg
http://www.filenook.net/Rough_Section_Home_Page.jpg
http://www.filenook.net/Rough_Section_Home_Page_2.jpg
Detailed document showing exact content required for the Main Home Page and each Section Home Page:
http://www.filenook.net/Home_Page_Content.gif
Target Market(s)
Mainly male, age 20 - 60. Not necessarily 'web savvy' or design-conscious
Industry/Entity Type
Advertising
Look and feel

```html
<!DOCTYPE html>
<html lang="en">
<head>
<meta charset="utf-8">
<title>Aviation Section Home Page</title>
<link rel="stylesheet" href="https://fonts.googleapis.com/css2?family=Noto+Sans:wght@400;700&family=Arimo:ital,wght@0,400;0,700;1,700&display=swap">
<style>
  :root {
    --sky: #b5d1ee;
    --steel: #7392b6;
    --title-teal: #17698c;
    --ink: #111111;
    --heading-red: #b00d0d;
    --button-top: #3a3a3a;
    --button-bottom: #050505;
    --arrow-blue: #2d8fd6;
    --card-edge: #1c1c1c;
    --card-fill: #f1f1f3;
    --ad-grey: #87888c;
    --divider: #d5d5d5;
  }
  * { box-sizing: border-box; margin: 0; padding: 0; }
  html, body { width: 926px; height: 1200px; overflow: hidden; background: #ffffff; }
  body { position: relative; font-family: "Arimo", Arial, sans-serif; color: var(--ink); }

  .intro { position: absolute; left: 0; top: 0; width: 926px; height: 343px; background: var(--sky); }
  .section-title {
    position: absolute; left: 22px; top: 16px;
    font-family: "Noto Sans", Verdana, sans-serif; font-weight: 700; font-size: 31px;
    color: var(--title-teal); letter-spacing: 0.2px;
  }
  .intro-text {
    position: absolute; left: 22px; top: 64px; width: 584px;
    font-family: "Noto Sans", Verdana, sans-serif; font-size: 15px; line-height: 20.5px;
    text-align: justify; color: var(--ink);
  }
  .action {
    position: absolute; width: 278px; height: 57px; border-radius: 4px;
    background: linear-gradient(var(--button-top), var(--button-bottom));
    box-shadow: 0 4px 6px rgba(0,0,0,0.35);
    color: #ffffff; font-family: "Noto Sans", Verdana, sans-serif; font-size: 19px;
    display: flex; align-items: center; text-decoration: none;
  }
  .action-label { width: 244px; text-align: center; }
  .action-arrow {
    width: 34px; height: 100%; border-left: 1px solid #555;
    display: flex; align-items: center; justify-content: center;
  }
  .action-search { left: 22px; top: 187px; }
  .action-buy { left: 325px; top: 187px; }
  .action-read { left: 22px; top: 263px; }
  .action-sell { left: 325px; top: 263px; }

  .mascot-panel {
    position: absolute; left: 629px; top: 21px; width: 276px; height: 276px;
    border: 3px solid #111; border-radius: 14px;
    background: linear-gradient(150deg, #c9443f 0%, #d97e6f 35%, #7e8c96 60%, #3c5fa8 100%);
  }

  .features { position: absolute; left: 0; top: 343px; width: 926px; height: 352px; background: var(--steel); }
  .feature-card {
    position: absolute; top: 41px; width: 275px; height: 275px;
    border: 2px solid var(--card-edge); border-radius: 16px; overflow: hidden;
    background: radial-gradient(ellipse 140% 60% at 0% 100%, #e7e7ea 60%, var(--card-fill) 61%);
  }
  .feature-card::before {
    content: ""; position: absolute; left: 0; top: 0; width: 100%; height: 55px;
    background: #ffffff; border-bottom: 1px solid #9a9a9a;
  }
  .card-one { left: 22px; }
  .card-two { left: 325px; }
  .card-three { left: 627px; }

  .articles { position: absolute; left: 0; top: 695px; width: 926px; height: 505px; }
  .article-list { position: absolute; left: 19px; top: 16px; width: 400px; }
  .article-heading {
    font-family: "Arimo", Arial, sans-serif; font-weight: 700; font-size: 17.5px;
    color: var(--heading-red); letter-spacing: 0.6px; margin-bottom: 9px;
  }
  .article-body { font-size: 14px; line-height: 18px; margin-bottom: 14px; }
  .column-divider { position: absolute; left: 455px; top: 20px; width: 1px; height: 490px; background: var(--divider); }
  .advert-slot {
    position: absolute; left: 493px; top: 18px; width: 415px; height: 346px;
    background: var(--ad-grey); display: flex; align-items: center; justify-content: center;
    color: #ffffff; font-weight: 700; font-style: italic; font-size: 19px; letter-spacing: 1px;
  }
  .side-story { position: absolute; left: 493px; top: 376px; width: 415px; }
</style>
</head>
<body>
  <header class="intro">
    <h1 class="section-title">Aviation Magazine title</h1>
    <p class="intro-text">Lorem ipsum dolor sit amet, consectetur adipisicing elit, sed do eiusmod tempor incididunt ut labore et dolore magna aliqua. Ut enim ad minim veniam, quis nostrud exercitation ullamco laboris nisi ut aliquip ex ea commodo consequat. Duis aute irure dolor in reprehenderit in voluptate velit esse cillum dolore eu fugiat nulla pariatur.</p>

    <a class="action action-search" href="#"><span class="action-label">SEARCH for articles</span><span class="action-arrow"><svg width="12" height="14" viewBox="0 0 12 14"><path d="M1 0 L12 7 L1 14 Z" fill="#2d8fd6"/></svg></span></a>
    <a class="action action-buy" href="#"><span class="action-label">BUY back issues</span><span class="action-arrow"><svg width="12" height="14" viewBox="0 0 12 14"><path d="M1 0 L12 7 L1 14 Z" fill="#2d8fd6"/></svg></span></a>
    <a class="action action-read" href="#"><span class="action-label">READ issues online</span><span class="action-arrow"><svg width="12" height="14" viewBox="0 0 12 14"><path d="M1 0 L12 7 L1 14 Z" fill="#2d8fd6"/></svg></span></a>
    <a class="action action-sell" href="#"><span class="action-label">SELL your magazines</span><span class="action-arrow"><svg width="12" height="14" viewBox="0 0 12 14"><path d="M1 0 L12 7 L1 14 Z" fill="#2d8fd6"/></svg></span></a>

    <div class="mascot-panel" role="img" aria-label="Cartoon mascot in blue overalls standing in front of an aviation magazine cover"></div>
  </header>

  <section class="features">
    <div class="feature-card card-one"></div>
    <div class="feature-card card-two"></div>
    <div class="feature-card card-three"></div>
  </section>

  <main class="articles">
    <div class="article-list">
      <h2 class="article-heading">Lorem ipsum dolor sit ame</h2>
      <p class="article-body">Lorem ipsum dolor sit amet, consectetur adipisic-<br>ing elit, sed do eiusmod tempor incididunt ut labore et<br>dolore magna aliqua. Ut enim ad minim veniam, quis<br>nostrud exercitation ullamco laboris nisi ut aliquip<br>ex ea commodo consequat. Duis aute irure dolor in<br>reprehenderit in voluptate velit esse cillum dolore eu<br>fugiat nulla pariatur. Excepteur sint occaecat cupidatat</p>
      <h2 class="article-heading">Lorem ipsum dolor sit ame</h2>
      <p class="article-body">Lorem ipsum dolor sit amet, consectetur adipisic-<br>ing elit, sed do eiusmod tempor incididunt ut labore et<br>dolore magna aliqua. Ut enim ad minim veniam, quis<br>nostrud exercitation ullamco laboris nisi ut aliquip<br>ex ea commodo consequat. Duis aute irure dolor in<br>reprehenderit in voluptate velit esse cillum dolore eu<br>fugiat nulla pariatur. Excepteur sint occaecat cupidatat</p>
      <h2 class="article-heading">Lorem ipsum dolor sit ame</h2>
      <p class="article-body">Lorem ipsum dolor sit amet, consectetur adipisic-<br>ing elit, sed do eiusmod tempor incididunt ut labore et<br>dolore magna aliqua. Ut enim ad minim veniam, quis<br>nostrud exercitation ullamco laboris nisi ut aliquip<br>ex ea commodo consequat. Duis aute irure dolor in</p>
    </div>
    <div class="column-divider"></div>
    <div class="advert-slot">300x250 px</div>
    <div class="side-story">
      <h2 class="article-heading">Lorem ipsum dolor sit ame</h2>
      <p class="article-body">Lorem ipsum dolor sit amet, consectetur adipisic-<br>ing elit, sed do eiusmod tempor incididunt ut labore et<br>dolore magna aliqua. Ut enim ad minim veniam, quis<br>nostrud exercitation ullamco laboris nisi ut aliquip<br>ex ea commodo consequat. Duis aute irure dolor in</p>
    </div>
  </main>
</body>
</html>
```